Business Card for Coastal Tundrabridge Advisory

We need a business card for Coastal Tundrabridge Advisory. The company website address is provided below. The company logo is attached. We provide specialized permafrost services to the mining, transportation, and oil & gas industries. The card should be prepared for:
Matthias Korhonen, PhD.
Coastal Tundrabridge Advisory
PO Box 418259
Quillwater, Alaska 99642
Direct: +1-907-555-0143
Email: mkorhonen@tundrabridgeadvisory.example
Website: www.coastaltundrabridgeadvisory.example

```html
<!DOCTYPE html>
<html lang="en">
<head>
<meta charset="utf-8">
<title>Coastal Tundrabridge Advisory – Business Card</title>
<link rel="stylesheet" href="https://fonts.googleapis.com/css2?family=Montserrat:wght@300;600;700&family=Roboto:wght@400;500;700&display=swap">
<style>
  :root {
    --page-bg: #e9e7e3;
    --card-navy: #121a27;
    --card-navy-deep: #0e1520;
    --accent-blue: #2a6f9e;
    --accent-blue-soft: #1c4566;
    --text-white: #ffffff;
    --text-soft: #dfe5ec;
    --rule: #8a94a3;
  }
  * { box-sizing: border-box; margin: 0; padding: 0; }
  html, body {
    width: 1200px; height: 780px; overflow: hidden;
    background: var(--page-bg);
  }
  .canvas {
    position: relative; width: 1200px; height: 780px;
    display: flex; align-items: center; justify-content: center; gap: 40px;
  }
  .card {
    position: relative; width: 540px; height: 309px;
    background: var(--card-navy);
    color: var(--text-white);
    overflow: hidden;
    box-shadow: 0 10px 24px rgba(0,0,0,0.18);
  }

  /* Front */
  .holder {
    position: absolute; left: 26px; top: 128px;
    font-family: "Montserrat", sans-serif; font-size: 22px; line-height: 1;
    white-space: nowrap;
  }
  .holder__first { font-weight: 700; }
  .holder__last { font-weight: 300; letter-spacing: 0.5px; }
  .holder__title {
    position: absolute; right: 0; top: 28px;
    font-family: "Montserrat", sans-serif; font-weight: 700; font-size: 13px;
  }
  .divider {
    position: absolute; left: 258px; top: 92px; width: 1px; height: 84px;
    background: var(--rule);
  }
  .contacts {
    position: absolute; left: 274px; top: 98px;
    list-style: none;
    font-family: "Roboto", sans-serif; font-size: 10.5px; color: var(--text-soft);
  }
  .contacts__item {
    display: flex; align-items: center; gap: 7px; height: 20px;
    white-space: nowrap;
  }
  .contacts__icon { width: 11px; height: 11px; flex: none; }
  .address {
    position: absolute; left: 274px; bottom: 44px;
    font-family: "Roboto", sans-serif; font-size: 11px; color: var(--text-soft);
    white-space: nowrap;
  }

  /* Back */
  .card--back { background: var(--card-navy-deep); }
  .pattern-field {
    position: absolute; inset: 0;
    background:
      linear-gradient(100deg, var(--accent-blue) 0%, var(--accent-blue-soft) 28%, var(--card-navy) 55%, var(--card-navy-deep) 100%);
    opacity: 0.85;
  }
  .brand {
    position: absolute; left: 0; right: 0; top: 78px;
    text-align: center;
    font-family: "Montserrat", sans-serif; font-weight: 600; font-size: 17px;
    letter-spacing: 0.5px; color: var(--text-white);
  }
  .services {
    position: absolute; left: 0; right: 0; bottom: 34px;
    text-align: center; font-family: "Roboto", sans-serif;
  }
  .services__title {
    font-weight: 700; font-size: 12px; letter-spacing: 0.3px; margin-bottom: 6px;
  }
  .services__text { font-weight: 400; font-size: 10.5px; color: var(--text-soft); }
</style>
</head>
<body>
<main class="canvas">

  <section class="card card--front" aria-label="Card front">
    <h1 class="holder">
      <span class="holder__first">Matthias</span>
      <span class="holder__last">Korhonen</span>
      <span class="holder__title">PhD</span>
    </h1>
    <div class="divider"></div>
    <ul class="contacts">
      <li class="contacts__item">
        <svg class="contacts__icon" viewBox="0 0 24 24" aria-hidden="true"><path fill="#fff" d="M6.6 10.8a15.1 15.1 0 0 0 6.6 6.6l2.2-2.2a1 1 0 0 1 1-.25 11.4 11.4 0 0 0 3.6.57 1 1 0 0 1 1 1V20a1 1 0 0 1-1 1A17 17 0 0 1 3 4a1 1 0 0 1 1-1h3.5a1 1 0 0 1 1 1c0 1.25.2 2.45.57 3.57a1 1 0 0 1-.25 1z"/></svg>
        <span>+1-907-555-0143</span>
      </li>
      <li class="contacts__item">
        <svg class="contacts__icon" viewBox="0 0 24 24" aria-hidden="true"><rect x="2" y="5" width="20" height="14" rx="1.5" fill="#fff"/><path d="M3 6l9 7 9-7" fill="none" stroke="#121a27" stroke-width="1.8"/></svg>
        <span>mkorhonen@tundrabridgeadvisory.example</span>
      </li>
      <li class="contacts__item">
        <svg class="contacts__icon" viewBox="0 0 24 24" aria-hidden="true"><circle cx="12" cy="12" r="10" fill="#fff"/><path d="M2 12h20M12 2c3 3 3 17 0 20M12 2c-3 3-3 17 0 20" fill="none" stroke="#121a27" stroke-width="1.5"/></svg>
        <span>www.coastaltundrabridgeadvisory.example</span>
      </li>
    </ul>
    <p class="address">PO Box 418259 Quillwater, Alaska 99642</p>
  </section>

  <section class="card card--back" aria-label="Card back">
    <div class="pattern-field" role="img" aria-label="Repeating company wordmark pattern lit in blue from the left, fading into navy"></div>
    <p class="brand">Coastal Tundrabridge Advisory</p>
    <div class="services">
      <h2 class="services__title">OUR SERVICES</h2>
      <p class="services__text">We provide specialized permafrost services to the mining, transportation, and oil &amp; gas industries</p>
    </div>
  </section>

</main>
</body>
</html>
```